Animal Eye Clinic needs a Business card

We are a new veterinary ophthalmology practice (Ridgeline Pet Vision Care) and we need a business card designed. We only see animal eyes - we are not a regular veterinary clinic. We already have a logo. We are looking for a professional, good looking business card to hand out to our clients. We are looking for something simple but professional and contemporary. Our logo is likely the only picture/graphic that needs to be on the card.
Updates

Contact Information for Business Card

Delia Vossman, BSc, DVM, MSc, DipACVO
Veterinary Ophthalmologist

Phone: 250.418.3927
Email: ridgelinepetvisioncare@mailbox-example.net
Website: ridgelinepetvisioncare-example.net
Address: 1874 Thornbury Rd
Kelowna, BC, V1X 4M9

Colors

Designer to choose colors to be used in the design.

Requirements
Must have
• Our logo (attached)

```html
<!DOCTYPE html>
<html lang="en">
<head>
<meta charset="utf-8">
<title>Ridgeline Pet Vision Care – Business Card</title>
<link rel="stylesheet" href="https://fonts.googleapis.com/css2?family=Open+Sans:wght@400;600;700&display=swap">
<style>
  :root {
    --teal: #0897a8;
    --slate: #6b6b6b;
    --paper: #f4f4f4;
    --ink: #4a4a4a;
    --muted: #8a8a8a;
    --stage: #e4e5e6;
    --white: #ffffff;
  }
  * { box-sizing: border-box; margin: 0; padding: 0; }
  html, body {
    width: 1200px; height: 1015px; overflow: hidden;
    background: var(--stage);
    font-family: "Open Sans", Arial, sans-serif;
  }
  .canvas { position: relative; width: 1200px; height: 1015px; }

  .card {
    position: absolute; left: 250px; width: 700px; height: 400px;
    overflow: hidden; box-shadow: 0 6px 18px rgba(0,0,0,.18);
  }
  .card--back { top: 60px; background: var(--slate); }
  .card--front { top: 545px; background: var(--paper); }

  /* Brand lockup */
  .brand { position: absolute; display: flex; align-items: center; gap: 14px; }
  .brand__dot { width: 34px; height: 34px; border-radius: 50%; flex: none; }
  .brand__name { font-weight: 700; letter-spacing: .3px; white-space: nowrap; }

  .card--back .brand { left: 0; right: 0; top: 150px; justify-content: center; }
  .card--back .brand__dot { background: var(--white); }
  .card--back .brand__name { color: var(--white); font-size: 30px; }
  .back-stripe { position: absolute; left: 0; right: 0; top: 282px; height: 22px; background: var(--teal); }

  /* Front */
  .card--front .brand { left: 330px; top: 78px; }
  .card--front .brand__dot { background: var(--teal); width: 30px; height: 30px; }
  .card--front .brand__name { color: var(--teal); font-size: 22px; }

  .holder { position: absolute; left: 40px; top: 128px; }
  .holder__name { color: var(--teal); font-weight: 700; font-size: 22px; text-transform: uppercase; }
  .holder__creds { color: var(--muted); font-weight: 400; font-size: 15px; text-transform: none; }
  .holder__role { color: var(--ink); font-size: 15px; margin-top: 2px; }

  .address { position: absolute; right: 36px; top: 150px; text-align: right; color: var(--ink); font-size: 15px; line-height: 1.45; }

  .contacts { position: absolute; left: 150px; top: 196px; list-style: none; color: var(--ink); font-size: 15.5px; line-height: 1.55; }
  .contacts li { display: flex; align-items: center; gap: 8px; }
  .contacts svg { width: 14px; height: 14px; flex: none; fill: var(--teal); }

  .front-band { position: absolute; left: 0; right: 0; bottom: 0; height: 128px; background: var(--teal); }
</style>
</head>
<body>
<main class="canvas">
  <section class="card card--back" aria-label="Card back">
    <div class="brand">
      <span class="brand__dot"></span>
      <span class="brand__name">Ridgeline Pet Vision Care</span>
    </div>
    <div class="back-stripe"></div>
  </section>

  <section class="card card--front" aria-label="Card front">
    <div class="brand">
      <span class="brand__dot"></span>
      <span class="brand__name">Ridgeline Pet Vision Care</span>
    </div>

    <div class="holder">
      <p class="holder__name">Delia Vossman<span class="holder__creds">, BSc, DVM, MSc, DipACVO</span></p>
      <p class="holder__role">Veterinary Ophthalmologist</p>
    </div>

    <address class="address" style="font-style:normal">
      1874 Thornbury Rd<br>
      Kelowna, BC, V1X 4M9
    </address>

    <ul class="contacts">
      <li>
        <svg viewBox="0 0 16 16" aria-hidden="true"><path d="M3.5 1l2.5 3-1.5 2c.8 2 2.5 3.7 4.5 4.5l2-1.5 3 2.5-1.5 2.5C7 14 2 9 1 2.5z"/></svg>
        250.418.3927
      </li>
      <li>
        <svg viewBox="0 0 16 16" aria-hidden="true"><path d="M1 3h14v10H1z M2 4l6 5 6-5" fill="none" stroke="#0897a8" stroke-width="1.6"/></svg>
        ridgelinepetvisioncare@mailbox-example.net
      </li>
      <li>
        <svg viewBox="0 0 16 16" aria-hidden="true"><circle cx="8" cy="8" r="6.5" fill="none" stroke="#0897a8" stroke-width="1.5"/><path d="M1.5 8h13M8 1.5c-3 3.5-3 9.5 0 13M8 1.5c3 3.5 3 9.5 0 13" fill="none" stroke="#0897a8" stroke-width="1.2"/></svg>
        ridgelinepetvisioncare-example.net
      </li>
    </ul>

    <div class="front-band"></div>
  </section>
</main>
</body>
</html>
```